Brightway Carpet and Tile cleaning Business card Design

I need a design that has the same feel as my van.
i would also like a prominent "Review us online" somewhere, but not that it makes it look silly.
I would like the card to have a little bit of grey or black in the design as well.

It will need contact details
phone: 0455 817264
email: rkbrightwayclean@mailbox-example.com
website: www.brightwaycarpetandtilecleaning-example.com.au
facebook: /brightwaycarpetandtilecleaning

Industry/Entity Type

Business

Contact Information for Business Card

Phone number 0455817264
Email rkbrightwayclean@mailbox-example.com
Website www.brightwaycarpetandtilecleaning-example.com.au
Facebook/brightwaycarpetandtilecleaning

Colors
000000

Requirements
Must have
• Same feel as my van
• I want the card to stand out from the crowd
Nice to have
• Maybe include a tiny bit of a third colour? Grey's,blacks, orange?

```html
<!DOCTYPE html>
<html lang="en">
<head>
<meta charset="utf-8">
<title>Brightway Carpet and Tile Cleaning – Business Card</title>
<link rel="stylesheet" href="https://fonts.googleapis.com/css2?family=Roboto:wght@300;400;500&display=swap">
<style>
  :root {
    --backdrop: #bbbbbb;
    --card: #ffffff;
    --brand-blue: #0aaad9;
    --ink: #2b2b2b;
    --muted: #555555;
    --shadow: rgba(0, 0, 0, 0.35);
  }
  * { margin: 0; padding: 0; box-sizing: border-box; }
  html, body {
    width: 1200px; height: 1200px; overflow: hidden;
    background: var(--backdrop);
    font-family: "Roboto", sans-serif;
  }
  .stage { position: relative; width: 1200px; height: 1200px; }
  .card {
    position: absolute; width: 468px; height: 766px;
    background: var(--card);
    box-shadow: 12px 12px 6px var(--shadow);
  }
  .card--front { left: 107px; top: 184px; }
  .card--back  { left: 625px; top: 182px; }

  .brand {
    position: absolute; left: 0; right: 0;
    display: flex; align-items: center; justify-content: center; gap: 12px;
    color: var(--brand-blue); font-weight: 500;
  }
  .card--front .brand { top: 335px; }
  .card--back .brand { top: 118px; }
  .brand__dot {
    width: 26px; height: 26px; border-radius: 50%;
    background: var(--brand-blue); flex: none;
  }
  .brand__text { display: flex; flex-direction: column; line-height: 1; }
  .brand__name { font-size: 48px; letter-spacing: -0.5px; }
  .brand__tag { font-size: 14px; letter-spacing: 2.4px; margin-top: 6px; }

  .accent-bar { position: absolute; left: 57px; top: 266px; width: 352px; height: 16px; }

  .contact {
    position: absolute; left: 0; right: 0;
    text-align: center; color: var(--ink); font-weight: 300;
  }
  .contact__icon { display: block; margin: 0 auto 14px; width: 26px; height: 26px; }
  .contact__text { font-size: 20px; white-space: nowrap; }
  .contact--phone { top: 312px; }
  .contact--phone .contact__text { font-size: 21px; font-weight: 400; }
  .contact--email { top: 416px; }
  .contact--email .contact__text { font-size: 19px; }
  .contact--web { top: 517px; }
  .contact--web .contact__text { font-size: 15.5px; }
  .contact--social { top: 620px; }
  .contact--social .contact__text { font-size: 18px; color: var(--muted); }

  .divider {
    position: absolute; left: 57px; width: 342px; height: 2px;
    background: var(--brand-blue);
  }
  .divider--1 { top: 397px; }
  .divider--2 { top: 503px; }
  .divider--3 { top: 608px; }

  .review-button {
    position: absolute; left: 74px; top: 716px; width: 319px; height: 50px;
    background: var(--brand-blue); color: #fff;
    font-weight: 300; font-size: 19px;
    display: flex; align-items: center; justify-content: center;
  }
</style>
</head>
<body>
<main class="stage">

  <section class="card card--front" aria-label="Card front">
    <div class="brand">
      <span class="brand__dot"></span>
      <div class="brand__text">
        <span class="brand__name">Brightway</span>
        <span class="brand__tag">CARPET &amp; TILE CLEANING</span>
      </div>
    </div>
  </section>

  <section class="card card--back" aria-label="Card back">
    <div class="brand">
      <span class="brand__dot"></span>
      <div class="brand__text">
        <span class="brand__name">Brightway</span>
        <span class="brand__tag">CARPET &amp; TILE CLEANING</span>
      </div>
    </div>

    <svg class="accent-bar" viewBox="0 0 352 16" preserveAspectRatio="none" aria-hidden="true">
      <polygon points="5,0 347,0 352,16 0,16" fill="#0aaad9"/>
    </svg>

    <div class="contact contact--phone">
      <svg class="contact__icon" viewBox="0 0 26 26" aria-hidden="true">
        <rect x="1" y="1" width="24" height="24" fill="none" stroke="#0aaad9" stroke-width="1.6"/>
        <path d="M8.5 7.5c.6-.6 1.4-.5 1.8.1l1.2 1.8c.3.5.2 1.1-.2 1.5l-.7.6c.6 1.3 1.7 2.5 3 3.1l.6-.7c.4-.4 1-.5 1.5-.2l1.8 1.2c.6.4.7 1.2.1 1.8l-.8.8c-.7.7-1.8.8-2.7.4-2.8-1.3-5-3.5-6.3-6.3-.4-.9-.3-2 .4-2.7z" fill="#0aaad9"/>
      </svg>
      <span class="contact__text">0455 817264</span>
    </div>
    <div class="divider divider--1"></div>

    <div class="contact contact--email">
      <svg class="contact__icon" viewBox="0 0 26 26" aria-hidden="true">
        <rect x="1" y="1" width="24" height="24" fill="none" stroke="#0aaad9" stroke-width="1.6"/>
        <rect x="6.5" y="8.5" width="13" height="9" fill="#0aaad9"/>
        <path d="M6.5 8.5l6.5 5 6.5-5M6.5 17.5l4.5-4M19.5 17.5l-4.5-4" fill="none" stroke="#fff" stroke-width="1"/>
      </svg>
      <span class="contact__text">rkbrightwayclean@mailbox-example.com</span>
    </div>
    <div class="divider divider--2"></div>

    <div class="contact contact--web">
      <svg class="contact__icon" viewBox="0 0 26 26" aria-hidden="true">
        <rect x="1" y="1" width="24" height="24" fill="none" stroke="#0aaad9" stroke-width="1.6"/>
        <circle cx="13" cy="13" r="6" fill="none" stroke="#0aaad9" stroke-width="1.6"/>
        <path d="M7 13h12M13 7c-2 2-2 10 0 12M13 7c2 2 2 10 0 12" fill="none" stroke="#0aaad9" stroke-width="1.1"/>
      </svg>
      <span class="contact__text">www.brightwaycarpetandtilecleaning-example.com.au</span>
    </div>
    <div class="divider divider--3"></div>

    <div class="contact contact--social">
      <svg class="contact__icon" viewBox="0 0 26 26" aria-hidden="true">
        <rect x="1" y="1" width="24" height="24" fill="none" stroke="#0aaad9" stroke-width="1.6"/>
      </svg>
      <span class="contact__text">brightwaycarpetandtilecleaning</span>
    </div>

    <div class="review-button">Review us online</div>
  </section>

</main>
</body>
</html>
```